Travel Agency Website - Simple General

Need a 7 page simple design that is pretty repetitive. Need to be able to load quickly that is SEO optimized. Trying to give ideas on what they can do, be personal as we are local, but at the same time come across as professional and get information easily with little burden.

- Landing Page
- Brimwell Vacations Page
- Family Trips
- Road Trips from Texas
- Other Destinations
- About Us Page
- Contact Us Page

Target Market(s)

Families

Coding

Coded - Design and coding required

Number of Pages Required

5+ page

Colors

Designer to choose colors to be used in the design.

Requirements
Must have
• Like it to flow easily with our logo. Use that for colors, etc.

```html
<!DOCTYPE html>
<html lang="en">
<head>
<meta charset="utf-8">
<title>Wanderlark Travel – Website Page Set</title>
<link href="https://fonts.googleapis.com/css2?family=Lora:wght@400;500;600&family=Inter:wght@400;500;600&display=swap" rel="stylesheet">
<style>
:root{
  --cream:#faf7f2;
  --band:#f2eee6;
  --ink:#2b2a28;
  --muted:#8d8780;
  --line:#ebe5dc;
  --orange:#e0603a;
  --gold:#f2b632;
  --teal:#4a93a8;
  --sky:#86c9ec;
  --white:#ffffff;
}
*{box-sizing:border-box}
html,body{margin:0;padding:0}
body{width:1200px;height:1200px;overflow:hidden;background:var(--white);position:relative;font-family:"Inter",sans-serif;color:var(--ink)}
ul{list-style:none;margin:0;padding:0}
p{margin:0}

.page{position:absolute;width:273px;background:var(--cream);overflow:hidden;box-shadow:0 0 0 .4px #efece7}
.abs{position:absolute}

/* navigation */
.nav{position:absolute;top:0;left:0;width:100%;height:13.5px;display:flex;align-items:center;padding-left:84px;gap:14px;font-size:2.2px;background:var(--cream)}
.brand{display:flex;align-items:center;gap:1.5px;font-family:"Lora",serif;font-weight:600;font-size:3px;color:var(--teal)}
.brand-mark{width:8px;height:8px;border-radius:50%;border:.4px solid var(--teal)}
.links{display:flex;gap:4px;align-items:center}
.links li{padding:.6px 1.8px;border-radius:3px}
.links li.on{background:var(--orange);color:var(--white)}

/* hero */
.hero{position:absolute;top:13.5px;left:0;width:100%}
.hero-shade{position:absolute;inset:0;background:linear-gradient(90deg,rgba(0,0,0,.35),rgba(0,0,0,0) 70%)}
.hero-copy{position:absolute;left:82px;color:var(--white);width:80px}
.hero-eyebrow{font-size:1.6px;letter-spacing:.3px;text-transform:uppercase;color:var(--gold);margin-bottom:1px}
.hero-title{font-family:"Lora",serif;font-weight:500;font-size:8.4px;line-height:1;margin:0}
.accent{color:var(--gold)}
.hero-text{font-size:1.8px;line-height:1.4;margin-top:1.2px;opacity:.9}
.hero-actions{display:flex;gap:3px;margin-top:2.5px;align-items:center}

.btn{display:inline-block;background:var(--orange);color:var(--white);font-size:1.5px;padding:.8px 3px;border-radius:3px;white-space:nowrap}
.btn-ghost{font-size:1.5px;color:var(--white)}

/* section type */
.eyebrow{font-size:1.4px;letter-spacing:.3px;text-transform:uppercase;color:var(--teal)}
.h2{font-family:"Lora",serif;font-weight:500;font-size:4px;margin:0;color:var(--ink)}
.h3{font-family:"Lora",serif;font-weight:500;font-size:3.2px;margin:0;color:var(--ink)}
.lede{font-size:1.6px;color:var(--muted);line-height:1.4}
.center{text-align:center}

/* photo placeholders */
.photo{position:absolute;border-radius:1px}
.cap{position:absolute;font-size:1.5px;text-align:center;color:var(--ink)}

/* tables */
.table{position:absolute;background:var(--white);border-radius:1.2px;box-shadow:0 .4px 1.2px rgba(0,0,0,.08);padding:1px 2px}
.row{display:grid;grid-template-columns:5px 24px 1fr;font-size:1.3px;height:5px;align-items:center;border-bottom:.3px solid var(--line);color:#555}
.row:last-child{border-bottom:0}
.row.head{color:var(--muted);height:4px}
.row b{font-weight:600;color:var(--ink)}
.table.family .row{grid-template-columns:6px 26px 1fr}

/* forms */
.card{position:absolute;background:var(--white);border-radius:1.5px;box-shadow:0 .5px 1.6px rgba(0,0,0,.1);padding:3px 2.5px}
.form-title{font-family:"Lora",serif;font-size:2.6px;font-weight:500;margin:.5px 0 1.5px}
.label{font-size:1.2px;color:var(--ink);margin-top:1.4px}
.input{height:2.6px;background:var(--cream);border:.25px solid var(--line);border-radius:.6px;margin-top:.5px;font-size:1.1px;color:var(--muted);padding-left:1px;line-height:2.4px}
.input.tall{height:5px}
.pair{display:grid;grid-template-columns:1fr 1fr;gap:2px}
.opts{display:flex;flex-wrap:wrap;gap:.6px 2.5px;font-size:1.1px;color:#555;margin-top:.5px}
.opts span::before{content:"";display:inline-block;width:1px;height:1px;border:.25px solid #aaa;border-radius:50%;margin-right:.5px;vertical-align:middle}
.card .btn{margin-top:2px}

/* feature tiles */
.tile{position:absolute;background:var(--white);border-radius:1.2px;box-shadow:0 .4px 1.2px rgba(0,0,0,.08);padding:2px}
.tile i{display:block;width:2.6px;height:2.6px;border-radius:50%;background:#fbe3da;margin-bottom:1.3px}
.tile b{display:block;font-size:1.3px;font-weight:600}
.tile p{font-size:1.1px;color:var(--muted);line-height:1.35;margin-top:.4px}

/* team */
.member-name{font-size:1.4px;font-weight:600;text-align:center}
.member-role{font-size:1.1px;color:var(--muted);text-align:center;line-height:1.4}

/* footer */
.footer{position:absolute;left:0;bottom:0;width:100%;height:26px;background:linear-gradient(90deg,var(--teal),var(--sky));color:var(--white)}
.foot-mark{position:absolute;left:82px;top:4px;width:8px;height:8px;border-radius:1.2px;background:var(--white);opacity:.9}
.foot-about{position:absolute;left:82px;top:13.5px;width:32px;font-size:1.1px;line-height:1.4}
.foot-links{position:absolute;left:121px;top:4px;display:flex;gap:1px}
.foot-links li{font-size:1px;background:rgba(255,255,255,.3);padding:.4px 1.2px;border-radius:2px}
.foot-contact{position:absolute;left:158px;top:4px;font-size:1.1px;line-height:1.8}
.foot-social{display:flex;gap:1px;margin-top:.6px}
.foot-social i{width:2px;height:2px;border-radius:50%;background:rgba(255,255,255,.7)}
.foot-copy{position:absolute;left:82px;right:82px;bottom:2px;display:flex;justify-content:space-between;font-size:.9px;opacity:.85}
</style>
</head>
<body>

<!-- LANDING PAGE -->
<section class="page" style="left:106px;top:36px;height:241px">
  <header class="nav"><span class="brand"><i class="brand-mark"></i>Wanderlark</span><ul class="links"><li class="on">Home</li><li>About Us</li><li>Vacations ▾</li><li>Contact Us</li></ul></header>
  <div class="hero" style="height:117px;background:linear-gradient(180deg,#6e6aa0 0%,#b37082 22%,#6f6f9e 38%,#33558f 55%,#27437c 100%)" role="img" aria-label="Red suspension bridge over a bay at sunset">
    <div class="hero-shade"></div>
    <div class="hero-copy" style="bottom:9px">
      <p class="hero-eyebrow">Local family travel planners</p>
      <h1 class="hero-title">Wanderlark <span class="accent">Travel</span><br><span class="accent">Adventures</span></h1>
      <div class="hero-actions"><span class="btn">Plan a trip</span><span class="btn-ghost">Learn more</span></div>
    </div>
  </div>
  <div class="abs center" style="top:141px;left:0;width:100%">
    <p class="eyebrow">Where to next</p>
    <h2 class="h2">Handpicked American escapes</h2>
    <p class="lede">From magical kingdoms to open highways, we plan every detail so you simply go.</p>
  </div>
  <div class="photo" style="left:82px;top:156px;width:25px;height:32px;background:linear-gradient(#a9c3de,#8c8fa8)" role="img" aria-label="Castle at a theme park"></div>
  <div class="photo" style="left:110px;top:156px;width:25px;height:32px;background:linear-gradient(#c7d9e6,#d8c9b3)" role="img" aria-label="Family walking on a beach"></div>
  <div class="photo" style="left:138px;top:156px;width:25px;height:32px;background:linear-gradient(#9bb4c9,#8a6e58)" role="img" aria-label="Roadside diner on a road trip"></div>
  <div class="photo" style="left:166px;top:156px;width:25px;height:32px;background:linear-gradient(#7d93b0,#a4584a)" role="img" aria-label="City welcome sign at dusk"></div>
  <p class="cap" style="left:82px;top:190px;width:25px">Brimwell Vacations By Land or Sea</p>
  <p class="cap" style="left:110px;top:190px;width:25px">Family Trips USA</p>
  <p class="cap" style="left:138px;top:190px;width:25px">Texas Road Trips USA</p>
  <p class="cap" style="left:166px;top:190px;width:25px">Other Destinations USA</p>
  <span class="btn abs" style="left:88px;top:196px">Explore</span>
  <span class="btn abs" style="left:116px;top:196px">Explore</span>
  <span class="btn abs" style="left:144px;top:196px">Explore</span>
  <span class="btn abs" style="left:172px;top:196px">Explore</span>
  <footer class="footer">
    <i class="foot-mark"></i><p class="foot-about">Local planners helping families travel with less stress and more fun.</p>
    <ul class="foot-links"><li>Home</li><li>About Us</li><li>Vacations</li><li>Contact Us</li></ul>
    <div class="foot-contact"><p>☎ (555) 014-2207</p><p>✉ hello@wanderlark.travel</p><p>Follow our adventures</p><div class="foot-social"><i></i><i></i></div></div>
    <div class="foot-copy"><span>© 2024 Wanderlark Travel</span><span>All rights reserved</span></div>
  </footer>
</section>

<!-- ABOUT US -->
<section class="page" style="left:439px;top:42px;height:207px">
  <header class="nav"><span class="brand"><i class="brand-mark"></i>Wanderlark</span><ul class="links"><li>Home</li><li class="on">About Us</li><li>Vacations ▾</li><li>Contact Us</li></ul></header>
  <div class="hero" style="height:104px;background:linear-gradient(90deg,#9a9a97,#7d7c78 45%,#b3b2ae)" role="img" aria-label="Smiling travel team celebrating outdoors">
    <div class="hero-shade"></div>
    <div class="hero-copy" style="bottom:11px;width:60px">
      <h1 class="hero-title">Meet the <span class="accent">Team</span></h1>
      <p class="hero-text">The passionate people behind every unforgettable family journey we plan.</p>
    </div>
  </div>
  <h2 class="h2 abs center" style="top:124px;left:0;width:100%;font-size:3.4px">Our Dedicated <span class="accent">Team Members</span></h2>
  <div class="photo" style="left:82.5px;top:132px;width:20px;height:25px;background:linear-gradient(#ddd7ce,#9a8474)" role="img" aria-label="Portrait of team member"></div>
  <div class="photo" style="left:105px;top:132px;width:20px;height:25px;background:linear-gradient(#e2ddd5,#b7907d)" role="img" aria-label="Portrait of team member"></div>
  <div class="photo" style="left:127.5px;top:132px;width:20px;height:25px;background:linear-gradient(#d9d4cc,#8e8a86)" role="img" aria-label="Portrait of team member"></div>
  <div class="photo" style="left:150px;top:132px;width:20px;height:25px;background:linear-gradient(#e4dfd8,#6e6a66)" role="img" aria-label="Portrait of team member"></div>
  <div class="photo" style="left:172.5px;top:132px;width:20px;height:25px;background:linear-gradient(#dcd7cf,#5f5650)" role="img" aria-label="Portrait of team member"></div>
  <div class="abs" style="left:80.5px;top:158.5px;width:24px"><p class="member-name">Ava Carter</p><p class="member-role">Founder<br>(555) 014-2201</p></div>
  <div class="abs" style="left:103px;top:158.5px;width:24px"><p class="member-name">Lena Ruiz</p><p class="member-role">Trip Planner<br>(555) 014-2202</p></div>
  <div class="abs" style="left:125.5px;top:158.5px;width:24px"><p class="member-name">Owen Hale</p><p class="member-role">Road Trips<br>(555) 014-2203</p></div>
  <div class="abs" style="left:148px;top:158.5px;width:24px"><p class="member-name">Mia Tran</p><p class="member-role">Cruises<br>(555) 014-2204</p></div>
  <div class="abs" style="left:170.5px;top:158.5px;width:24px"><p class="member-name">Eli Brooks</p><p class="member-role">Family Trips<br>(555) 014-2205</p></div>
  <footer class="footer">
    <i class="foot-mark"></i><p class="foot-about">Local planners helping families travel with less stress and more fun.</p>
    <ul class="foot-links"><li>Home</li><li>About Us</li><li>Vacations</li><li>Contact Us</li></ul>
    <div class="foot-contact"><p>☎ (555) 014-2207</p><p>✉ hello@wanderlark.travel</p><p>Follow our adventures</p><div class="foot-social"><i></i><i></i></div></div>
    <div class="foot-copy"><span>© 2024 Wanderlark Travel</span><span>All rights reserved</span></div>
  </footer>
</section>

<!-- BRIMWELL VACATIONS -->
<section class="page" style="left:760px;top:47.5px;height:481px">
  <header class="nav"><span class="brand"><i class="brand-mark"></i>Wanderlark</span><ul class="links"><li>Home</li><li>About Us</li><li>Vacations ▾</li><li>Contact Us</li></ul></header>
  <div class="hero" style="height:104px;background:linear-gradient(180deg,#a9aeb3,#c8b8b4 35%,#8b8c92 65%,#4f5560)" role="img" aria-label="Crowded theme park street with colorful balloons">
    <div class="hero-shade"></div>
    <div class="hero-copy" style="bottom:12px">
      <h1 class="hero-title">Brimwell <span class="accent">Vacations</span></h1>
      <p class="hero-text">Parks, resorts and cruises planned with care.</p>
      <div class="hero-actions"><span class="btn">Plan my trip</span><span class="btn-ghost">See options</span></div>
    </div>
  </div>
  <div class="photo" style="left:82px;top:124px;width:26px;height:32px;background:linear-gradient(#8fb2de,#a6a2b5)" role="img" aria-label="Fairytale castle under blue sky"></div>
  <div class="photo" style="left:109.5px;top:124px;width:26px;height:32px;background:linear-gradient(#b9c48a,#c25a3e)" role="img" aria-label="Costumed characters at a parade"></div>
  <div class="photo" style="left:137px;top:124px;width:26px;height:32px;background:linear-gradient(#6ea0d8,#a9b6cc)" role="img" aria-label="Castle towers in daylight"></div>
  <div class="photo" style="left:164.5px;top:124px;width:26px;height:32px;background:linear-gradient(#d7c7b6,#d94f8a)" role="img" aria-label="Costumed character in pink dress"></div>

  <p class="eyebrow abs" style="left:95px;top:163px">Resorts &amp; parks</p>
  <h3 class="h3 abs" style="left:95px;top:166px">Brimwell World</h3>
  <div class="table" style="left:95px;top:171px;width:82px">
    <div class="row head"><span>#</span><span>Destination</span><span>Highlights</span></div>
    <div class="row"><span>1</span><b>Magic Park</b><span>Castle shows, parades and fireworks.</span></div>
    <div class="row"><span>2</span><b>Future Park</b><span>World pavilions and science rides.</span></div>
    <div class="row"><span>3</span><b>Studio Park</b><span>Movie sets and thrill coasters.</span></div>
    <div class="row"><span>4</span><b>Safari Park</b><span>Wild trails and live animal tours.</span></div>
    <div class="row"><span>5</span><b>Water Parks</b><span>Lazy rivers and wave pools.</span></div>
  </div>
  <h3 class="h3 abs" style="left:95px;top:203px">Brimwell Land</h3>
  <div class="table" style="left:95px;top:208px;width:82px">
    <div class="row head"><span>#</span><span>Destination</span><span>Highlights</span></div>
    <div class="row"><span>1</span><b>Classic Park</b><span>Original rides and main street.</span></div>
    <div class="row"><span>2</span><b>Adventure Park</b><span>Pier games and hero lands.</span></div>
    <div class="row"><span>3</span><b>Downtown</b><span>Shops, dining and evening music.</span></div>
    <div class="row"><span>4</span><b>Resort Hotels</b><span>Stay steps from the gates.</span></div>
    <div class="row"><span>5</span><b>Day Passes</b><span>Flexible tickets for every family.</span></div>
  </div>

  <div class="card" style="left:82px;top:246px;width:53px;height:71px">
    <p class="eyebrow">Start planning</p><p class="form-title">Plan my Brimwell trip</p>
    <p class="label">Which Brimwell destination?</p><div class="opts"><span>World</span><span>Land</span></div>
    <div class="pair"><div><p class="label">Adults</p><div class="input"></div></div><div><p class="label">Children</p><div class="input"></div></div></div>
    <div class="pair"><div><p class="label">Start date</p><div class="input">mm/dd</div></div><div><p class="label">End date</p><div class="input">mm/dd</div></div></div>
    <p class="label">Anything else?</p><div class="input tall">Tell us more</div>
    <span class="btn">Send request</span>
  </div>
  <div class="card" style="left:139px;top:246px;width:52px;height:71px">
    <p class="eyebrow">Set sail</p><p class="form-title">Plan my Brimwell cruise</p>
    <div class="pair"><div><p class="label">Guests</p><div class="input"></div></div><div><p class="label">Nights</p><div class="input"></div></div></div>
    <p class="label">Preferred ports</p><div class="opts"><span>Florida</span><span>Texas</span><span>California</span><span>Bahamas</span><span>Alaska</span><span>Mexico</span></div>
    <p class="label">Departure month</p><div class="input"></div>
    <p class="label">Cabin type</p><div class="opts"><span>Inside</span><span>Balcony</span><span>Suite</span></div>
    <p class="label">Notes</p><div class="input tall"></div>
    <span class="btn">Send request</span>
  </div>

  <div class="abs center" style="left:0;top:335px;width:100%">
    <p class="eyebrow">Our approach</p>
    <h3 class="h3">A vacation as unique as your family</h3>
    <p class="lede" style="width:70px;margin:.6px auto 0">Every family travels differently, so every plan we create fits your pace, budget and dreams.</p>
  </div>
  <div class="abs" style="left:0;top:356px;width:100%;height:48px;background:var(--band)"></div>
  <div class="abs center" style="left:0;top:366px;width:100%"><p class="eyebrow">What we do</p><h3 class="h3">Brimwell experiences we plan</h3></div>
  <div class="tile" style="left:82px;top:376px;width:24px;height:20px"><i></i><b>World Resorts</b><p>Park tickets, dining and hotel stays.</p></div>
  <div class="tile" style="left:110px;top:376px;width:24px;height:20px"><i></i><b>Land Resorts</b><p>Short breaks near the coast.</p></div>
  <div class="tile" style="left:138px;top:376px;width:24px;height:20px"><i></i><b>Cruise Line</b><p>Family sailings with kids clubs.</p></div>
  <div class="tile" style="left:166px;top:376px;width:24px;height:20px"><i></i><b>Guided Tours</b><p>Group trips around the world.</p></div>
  <div class="abs center" style="left:0;top:418px;width:100%">
    <h3 class="h3">Ready to make some magic?</h3>
    <p class="lede">Tell us your dream and we will handle the planning.</p>
    <span class="btn" style="margin-top:1.5px">Get started</span>
  </div>
  <footer class="footer">
    <i class="foot-mark"></i><p class="foot-about">Local planners helping families travel with less stress and more fun.</p>
    <ul class="foot-links"><li>Home</li><li>About Us</li><li>Vacations</li><li>Contact Us</li></ul>
    <div class="foot-contact"><p>☎ (555) 014-2207</p><p>✉ hello@wanderlark.travel</p><p>Follow our adventures</p><div class="foot-social"><i></i><i></i></div></div>
    <div class="foot-copy"><span>© 2024 Wanderlark Travel</span><span>All rights reserved</span></div>
  </footer>
</section>

<!-- FAMILY TRIPS -->
<section class="page" style="left:107.5px;top:560.5px;height:357px">
  <header class="nav"><span class="brand"><i class="brand-mark"></i>Wanderlark</span><ul class="links"><li>Home</li><li>About Us</li><li>Vacations ▾</li><li>Contact Us</li></ul></header>
  <div class="hero" style="height:104.5px;background:linear-gradient(180deg,#b4bfca,#8b9aa1 35%,#516b55 65%,#5d6a6e)" role="img" aria-label="Resort water park with palm trees and slides">
    <div class="hero-shade"></div>
    <div class="hero-copy" style="bottom:9px">
      <p class="hero-eyebrow">Fun for every age</p>
      <h1 class="hero-title">Family <span class="accent">Trips</span></h1>
      <p class="hero-text">Theme parks, beaches and resorts made easy for families.</p>
      <div class="hero-actions"><span class="btn">Plan my trip</span><span class="btn-ghost">See ideas</span></div>
    </div>
  </div>
  <div class="photo" style="left:82px;top:124px;width:26px;height:33px;background:linear-gradient(#9fb9cf,#7d6a4c)" role="img" aria-label="Theme park entrance gate"></div>
  <div class="photo" style="left:109.5px;top:124px;width:26px;height:33px;background:linear-gradient(#7fa3d3,#5f6f8c)" role="img" aria-label="Family in front of a landmark"></div>
  <div class="photo" style="left:137px;top:124px;width:26px;height:33px;background:linear-gradient(#6fa5d8,#c25a46)" role="img" aria-label="Water park slides"></div>
  <div class="photo" style="left:164.5px;top:124px;width:26px;height:33px;background:linear-gradient(#5c8fd4,#3d5da6)" role="img" aria-label="Roller coaster against the sky"></div>
  <p class="cap" style="left:82px;top:158px;width:26px">Adventure Park</p>
  <p class="cap" style="left:109.5px;top:158px;width:26px">Movie Studio Park</p>
  <p class="cap" style="left:137px;top:158px;width:26px">Water Park</p>
  <p class="cap" style="left:164.5px;top:158px;width:26px">Coaster Park</p>
  <h3 class="h3 abs" style="left:94px;top:168px;font-size:2.8px">Places to Visit</h3>
  <p class="abs" style="left:94px;top:174px;font-size:1.6px;font-weight:600">Trip A</p>
  <div class="table family" style="left:89px;top:178px;width:89px">
    <div class="row head"><span>#</span><span>Destination</span><span>Highlights</span></div>
    <div class="row"><span>1</span><b>Orlando</b><span>Theme parks, resorts and water fun.</span></div>
    <div class="row"><span>2</span><b>San Diego</b><span>Zoo, beaches and harbor cruises.</span></div>
    <div class="row"><span>3</span><b>Washington</b><span>Museums, monuments and history.</span></div>
    <div class="row"><span>4</span><b>Yellowstone</b><span>Geysers, wildlife and camping.</span></div>
    <div class="row"><span>5</span><b>Anaheim</b><span>Classic rides and family hotels.</span></div>
  </div>
  <p class="abs" style="left:94px;top:211px;font-size:1.6px;font-weight:600">Trip B</p>
  <div class="table family" style="left:89px;top:216px;width:89px">
    <div class="row head"><span>#</span><span>Destination</span><span>Highlights</span></div>
    <div class="row"><span>1</span><b>Smoky Mountains</b><span>Cabins, hiking and waterfalls.</span></div>
    <div class="row"><span>2</span><b>New York</b><span>Shows, parks and skyline views.</span></div>
    <div class="row"><span>3</span><b>Myrtle Beach</b><span>Boardwalk, sand and mini golf.</span></div>
    <div class="row"><span>4</span><b>Hawaii</b><span>Snorkeling, luaus and volcanoes.</span></div>
    <div class="row"><span>5</span><b>Chicago</b><span>Lakefront, museums and deep dish.</span></div>
  </div>
  <div class="photo" style="left:89px;top:253px;width:46px;height:61px;background:linear-gradient(#4f9ed8,#a9d4ec 55%,#e8dcc5)" role="img" aria-label="Lifeguard tower on a sunny beach"></div>
  <div class="card" style="left:138px;top:253px;width:45px;height:61px">
    <p class="eyebrow">Start planning</p><p class="form-title">Plan my family trip</p>
    <p class="label">Have you been before?</p><div class="opts"><span>Yes</span><span>No</span></div>
    <p class="label">How many people?</p><div class="input"></div>
    <div class="pair"><div><p class="label">Start date</p><div class="input">mm/dd</div></div><div><p class="label">Duration</p><div class="input">days</div></div></div>
    <p class="label">Which trip do you prefer?</p><div class="opts"><span>Trip A</span><span>Trip B</span><span>Both</span></div>
    <p class="label">Notes</p><div class="input tall"></div>
    <span class="btn">Send request</span>
  </div>
  <footer class="footer">
    <i class="foot-mark"></i><p class="foot-about">Local planners helping families travel with less stress and more fun.</p>
    <ul class="foot-links"><li>Home</li><li>About Us</li><li>Vacations</li><li>Contact Us</li></ul>
    <div class="foot-contact"><p>☎ (555) 014-2207</p><p>✉ hello@wanderlark.travel</p><p>Follow our adventures</p><div class="foot-social"><i></i><i></i></div></div>
    <div class="foot-copy"><span>© 2024 Wanderlark Travel</span><span>All rights reserved</span></div>
  </footer>
</section>

<!-- TEXAS ROAD TRIPS -->
<section class="page" style="left:439px;top:567px;height:264px">
  <header class="nav"><span class="brand"><i class="brand-mark"></i>Wanderlark</span><ul class="links"><li>Home</li><li>About Us</li><li>Vacations ▾</li><li>Contact Us</li></ul></header>
  <div class="hero" style="height:104px;background:linear-gradient(180deg,#8d949a,#b2b6b6 35%,#6d6f6c 60%,#6e6352)" role="img" aria-label="Row of spray-painted cars half buried in a field">
    <div class="hero-shade"></div>
    <div class="hero-copy" style="bottom:10px">
      <h1 class="hero-title">Texas <span class="accent">Road Trips</span></h1>
      <p class="hero-text">Wide skies, quirky stops and unforgettable roadside wonders.</p>
      <div class="hero-actions"><span class="btn">Plan my trip</span></div>
    </div>
  </div>
  <div class="photo" style="left:82px;top:124px;width:26px;height:32px;background:linear-gradient(#7eaed6,#7d6b4e)" role="img" aria-label="Roadside town street"></div>
  <div class="photo" style="left:109.5px;top:124px;width:26px;height:32px;background:linear-gradient(#7fa9cf,#b9953e)" role="img" aria-label="Giant roadside sculpture"></div>
  <div class="photo" style="left:137px;top:124px;width:26px;height:32px;background:linear-gradient(#c8cfd4,#9c9d98)" role="img" aria-label="Surfer on gulf waves"></div>
  <div class="photo" style="left:164.5px;top:124px;width:26px;height:32px;background:linear-gradient(#c9b9a6,#5d4a3e)" role="img" aria-label="Outdoor market crowd"></div>
  <div class="photo" style="left:89px;top:164px;width:46px;height:58px;background:linear-gradient(#3c7fcf,#8fb8dc 55%,#8c6e56)" role="img" aria-label="Vintage truck at an old gas station"></div>
  <div class="card" style="left:139px;top:164px;width:43px;height:58px">
    <p class="eyebrow">Hit the road</p><p class="form-title">Plan my Texas road trip</p>
    <p class="label">Have you driven before?</p><div class="opts"><span>Yes</span><span>No</span></div>
    <p class="label">How many people?</p><div class="input"></div>
    <p class="label">Do you want a rental car?</p><div class="opts"><span>Yes</span><span>No</span></div>
    <div class="pair"><div><p class="label">Start date</p><div class="input">mm/dd</div></div><div><p class="label">End date</p><div class="input">mm/dd</div></div></div>
    <p class="label">Notes</p><div class="input tall"></div>
    <span class="btn">Send request</span>
  </div>
  <footer class="footer">
    <i class="foot-mark"></i><p class="foot-about">Local planners helping families travel with less stress and more fun.</p>
    <ul class="foot-links"><li>Home</li><li>About Us</li><li>Vacations</li><li>Contact Us</li></ul>
    <div class="foot-contact"><p>☎ (555) 014-2207</p><p>✉ hello@wanderlark.travel</p><p>Follow our adventures</p><div class="foot-social"><i></i><i></i></div></div>
    <div class="foot-copy"><span>© 2024 Wanderlark Travel</span><span>All rights reserved</span></div>
  </footer>
</section>

<!-- OTHER DESTINATIONS -->
<section class="page" style="left:760px;top:564px;height:272px">
  <header class="nav"><span class="brand"><i class="brand-mark"></i>Wanderlark</span><ul class="links"><li>Home</li><li>About Us</li><li>Vacations ▾</li><li>Contact Us</li></ul></header>
  <div class="hero" style="height:105.5px;background:linear-gradient(180deg,#4a4e4e,#6a6d66 35%,#8a7a44 60%,#3b3a35)" role="img" aria-label="Vintage yellow streetcar on a city street">
    <div class="hero-shade"></div>
    <div class="hero-copy" style="bottom:11px">
      <h1 class="hero-title">Other <span class="accent">Destinations</span></h1>
      <p class="hero-text">Cities, coasts and hidden gems across America.</p>
      <div class="hero-actions"><span class="btn">Plan my trip</span></div>
    </div>
  </div>
  <div class="photo" style="left:82.5px;top:126px;width:26px;height:33px;background:linear-gradient(#8f5c48,#4a3a34)" role="img" aria-label="City street with tall buildings"></div>
  <div class="photo" style="left:110px;top:126px;width:26px;height:33px;background:linear-gradient(#6fb0e0,#3f8fb0)" role="img" aria-label="Tropical beach and ocean"></div>
  <div class="photo" style="left:137.5px;top:126px;width:26px;height:33px;background:linear-gradient(#9ac0de,#4f6a46)" role="img" aria-label="Palm-lined avenue"></div>
  <div class="photo" style="left:165px;top:126px;width:26px;height:33px;background:linear-gradient(#6e7f94,#2c3038)" role="img" aria-label="Skyscraper spire"></div>
  <p class="cap" style="left:82.5px;top:160px;width:26px">Chicago</p>
  <p class="cap" style="left:110px;top:160px;width:26px">Hawaii Beach</p>
  <p class="cap" style="left:137.5px;top:160px;width:26px">Palm Springs</p>
  <p class="cap" style="left:165px;top:160px;width:26px">New York</p>
  <div class="card" style="left:105.5px;top:168px;width:62.5px;height:61px">
    <p class="eyebrow">Start planning</p><p class="form-title">Plan my trip</p>
    <p class="label">Where would you like to go?</p><div class="opts"><span>City</span><span>Beach</span><span>Mountains</span><span>Other</span></div>
    <p class="label">How would you like to travel?</p><div class="opts"><span>Fly</span><span>Drive</span><span>Train</span></div>
    <p class="label">How many people?</p><div class="input"></div>
    <div class="pair"><div><p class="label">Start date</p><div class="input">mm/dd</div></div><div><p class="label">End date</p><div class="input">mm/dd</div></div></div>
    <p class="label">Notes</p><div class="input tall"></div>
    <span class="btn">Send request</span>
  </div>
  <footer class="footer">
    <i class="foot-mark"></i><p class="foot-about">Local planners helping families travel with less stress and more fun.</p>
    <ul class="foot-links"><li>Home</li><li>About Us</li><li>Vacations</li><li>Contact Us</li></ul>
    <div class="foot-contact"><p>☎ (555) 014-2207</p><p>✉ hello@wanderlark.travel</p><p>Follow our adventures</p><div class="foot-social"><i></i><i></i></div></div>
    <div class="foot-copy"><span>© 2024 Wanderlark Travel</span><span>All rights reserved</span></div>
  </footer>
</section>

<!-- CONTACT US -->
<section class="page" style="left:440px;top:945.5px;height:217px">
  <header class="nav"><span class="brand"><i class="brand-mark"></i>Wanderlark</span><ul class="links"><li>Home</li><li>About Us</li><li>Vacations ▾</li><li class="on">Contact Us</li></ul></header>
  <div class="hero" style="height:103.5px;background:linear-gradient(180deg,#4b4049,#7c5048 35%,#b2663c 55%,#5a3a2c 75%,#2f2622)" role="img" aria-label="Desert buttes under a sunset sky">
    <div class="hero-shade"></div>
    <div class="hero-copy" style="bottom:11px">
      <p class="hero-eyebrow">Get in touch</p>
      <h1 class="hero-title">Contact Us</h1>
      <p class="hero-text">Let's start planning your next unforgettable adventure together.</p>
    </div>
  </div>
  <div class="photo" style="left:90px;top:124.5px;width:47px;height:53px;background:linear-gradient(#9fc3e0,#7d8ea0 45%,#5d6d4c)" role="img" aria-label="Mountain overlook with green valley"></div>
  <div class="card" style="left:139px;top:124.5px;width:44.5px;height:53px">
    <p class="form-title" style="font-size:3px">Send Us a <span class="accent">Message</span></p>
    <p class="lede" style="font-size:1.2px">We would love to hear from you. Fill out the form and we will reply soon.</p>
    <p class="label">Name</p><div class="input"></div>
    <div class="pair"><div><p class="label">Email</p><div class="input"></div></div><div><p class="label">Phone</p><div class="input"></div></div></div>
    <p class="label">How can we help?</p><div class="input tall"></div>
    <span class="btn">Send message</span>
  </div>
  <footer class="footer">
    <i class="foot-mark"></i><p class="foot-about">Local planners helping families travel with less stress and more fun.</p>
    <ul class="foot-links"><li>Home</li><li>About Us</li><li>Vacations</li><li>Contact Us</li></ul>
    <div class="foot-contact"><p>☎ (555) 014-2207</p><p>✉ hello@wanderlark.travel</p><p>Follow our adventures</p><div class="foot-social"><i></i><i></i></div></div>
    <div class="foot-copy"><span>© 2024 Wanderlark Travel</span><span>All rights reserved</span></div>
  </footer>
</section>

</body>
</html>
```